Emergency Management Consulting Needs a Website

Need to develop a website for an Emergency Management Consulting business. This website needs to be user friendly and resemble disaster preparedness, response, recovery, and mitigation. It must allow for me to make changes to it myself by adding pages, content and pictures. Looking for an advanced page to the website that allows monitoring of social media sites, hashtags, and keywords. Must have pictures of disasters on the site. Must try to integrate the logo colors, not excessive.

Reason: Did not receive anything sufficient to what I am looking for.

Industry/Entity Type

Government

Coding

Coded - Design and coding required

Number of Pages Required

5+ page

Requirements
Must have
• Logo, advanced social media monitoring page, allow for edits myself (content, pages, graphics) this must be a CMS of some sort, use logo color scheme (not excessively), must be professional looking, connect with Plivex Domain, find a hosting site, SEO, no "long" designs, minimize "dead" space, no social media feeds, no newsletter stuff.
• Menu items: Home, About Us, Services, Situation Monitor, Work With Us, Contact Us (hopefully these could be editable if I need to later)
• When you make a submission, please send me a message on which CMS you are using. Thank you.
Nice to have
• Examples of websites:
• https://www.qrt.vic.gov.au/
• http://www.larkenmoss.example/
• http://www.tulpaxo.example/
• http://vonmirelconsulting.example/
• http://www.calvornet.example/services/emergency-management
• https://zuq.example/
• http://www.vestimora.example/Responsibility/Sustainable-Development/HSE/Crisis-and-Emergency-Management/

```html
<!DOCTYPE html>
<html lang="en">
<head>
<meta charset="utf-8">
<title>Kestral Ford – Emergency Management Consulting</title>
<link href="https://fonts.googleapis.com/css2?family=Raleway:wght@400;500;600;700&family=Open+Sans:wght@400;600;700&display=swap" rel="stylesheet">
<style>
:root{
  --orange:#f39c1f;
  --ink:#333333;
  --muted:#7a7a7a;
  --line:#e6e6e6;
  --soft:#f6f6f6;
  --footer:#2c2c2c;
  --footer-bar:#232323;
  --footer-text:#b5b5b5;
  --white:#ffffff;
}
*{margin:0;padding:0;box-sizing:border-box}
html,body{width:1200px;height:4302px;overflow:hidden;background:var(--white)}
body{position:relative;font-family:'Open Sans',sans-serif;color:var(--ink)}
.abs{position:absolute}
.heading{font-family:'Raleway',sans-serif;font-weight:600;color:var(--ink);text-transform:uppercase}
.center{text-align:center}
.para{font-size:12.5px;line-height:26.5px;color:var(--muted)}
.btn{position:absolute;background:var(--orange);color:var(--white);font-weight:700;font-size:12px;letter-spacing:.6px;display:flex;align-items:center;justify-content:center;text-transform:uppercase}

/* header */
.site-header{top:0;left:0;width:1200px;height:77px;background:var(--white);box-shadow:0 1px 3px rgba(0,0,0,.12);z-index:3}
.brand{left:46px;top:21px;display:flex;align-items:center;gap:10px}
.brand-dot{width:34px;height:34px;border-radius:50%;background:var(--orange)}
.brand-name{font-family:'Raleway',sans-serif;font-weight:700;font-size:24px;color:var(--ink);letter-spacing:.5px;line-height:1}
.main-nav{left:300px;top:31px;width:650px;display:flex;justify-content:space-between;align-items:center}
.nav-item{font-size:11px;font-weight:600;color:var(--ink);letter-spacing:.3px;white-space:nowrap}
.nav-item .caret{display:inline-block;margin-left:6px;font-size:9px;color:#777}
.nav-phone{left:985px;top:27px;display:flex;align-items:center;gap:8px;color:var(--orange);font-size:17px;font-weight:600;white-space:nowrap}

/* hero */
.hero{top:77px;left:0;width:1200px;height:614px;background:linear-gradient(120deg,#6f6560 0%,#8a3b35 30%,#a8a29a 55%,#7a7470 75%,#4f5358 100%)}
.hero-shade{top:77px;left:0;width:1200px;height:614px;background:rgba(20,20,25,.35)}
.hero-title{top:278px;left:0;width:1200px;font-family:'Raleway',sans-serif;font-weight:600;font-size:48px;letter-spacing:7px;color:var(--white)}
.hero-sub{top:345px;left:0;width:1200px;font-family:'Raleway',sans-serif;font-size:22px;letter-spacing:3px;color:var(--white)}
.hero-arrow{top:365px;width:20px;height:28px}
.hero-down{left:579px;top:606px;width:40px;height:40px;border:1.5px solid var(--white);border-radius:50%}

/* consulting */
.service-icon{top:958px;width:114px;height:114px;background:var(--orange)}
.service-icon::after{content:"";position:absolute;inset:6px;border:3px solid var(--white)}
.service-label{top:1100px;width:330px;font-family:'Raleway',sans-serif;font-weight:600;font-size:14px;color:var(--ink)}
.service-text{top:1132px;width:280px}

/* about */
.about-photo{left:98px;top:1302px;width:481px;height:355px;background:linear-gradient(135deg,#f7d77a 0%,#e9b25a 25%,#9ba3a8 55%,#b33b33 75%,#5c6570 100%)}

/* band */
.band-photo{top:1746px;left:0;width:1200px;height:567px;background:linear-gradient(100deg,#5b4a33 0%,#8e7a4f 25%,#b69a3c 45%,#6e6a62 70%,#4f5255 100%)}
.band-box{left:537px;top:1866px;width:620px;height:339px;background:var(--orange)}
.band-title{left:55px;top:45px;font-family:'Raleway',sans-serif;font-weight:600;font-size:26px;color:var(--white)}
.band-text{left:55px;width:520px;font-size:12px;line-height:26.5px;color:var(--white)}
.band-btn{left:55px;top:248px;width:174px;height:42px;border:2px solid var(--white);color:var(--white);font-size:12px;font-weight:700;letter-spacing:.6px;display:flex;align-items:center;justify-content:center}

/* news */
.news-photo{width:306px;height:207px}
.news-title{font-weight:700;font-size:13px;color:var(--ink);letter-spacing:.2px}
.news-date{font-size:11.5px;color:var(--muted)}

/* quote */
.quote-band{top:3184px;left:0;width:1200px;height:421px;background:linear-gradient(110deg,#3a3a36 0%,#5d5a52 35%,#4a4d4a 60%,#2f3232 100%)}
.quote-shade{top:3184px;left:0;width:1200px;height:421px;background:rgba(0,0,0,.35)}
.quote-text{top:3368px;left:200px;width:800px;font-size:17px;line-height:31px;color:var(--white)}
.quote-author{top:3457px;left:0;width:1200px;font-family:'Raleway',sans-serif;font-size:22px;color:var(--orange)}
.dot{top:3548px;width:9px;height:9px;border-radius:50%;background:#8b8b8b}

/* situation monitor */
.monitor-title{top:3660px;left:0;width:1200px;font-size:27px;font-weight:500}
.monitor-card{top:3735px;width:306px;height:200px;border:1px solid var(--line);background:var(--soft)}
.monitor-tag{left:24px;top:22px;font-size:14px;font-weight:700;color:var(--orange)}
.monitor-label{left:24px;top:50px;font-size:11px;color:var(--muted)}
.monitor-count{left:24px;top:78px;font-family:'Raleway',sans-serif;font-size:32px;font-weight:600;color:var(--ink)}
.monitor-bar{left:24px;top:138px;width:258px;height:6px;background:var(--line)}
.monitor-fill{position:absolute;left:0;top:0;height:6px;background:var(--orange)}
.monitor-note{left:24px;top:160px;font-size:11px;color:var(--muted)}

/* footer */
.site-footer{top:3990px;left:0;width:1200px;height:247px;background:var(--footer)}
.footer-bar{top:4237px;left:0;width:1200px;height:65px;background:var(--footer-bar)}
.f-title{top:4033px;font-size:12.5px;font-weight:700;color:var(--white);letter-spacing:.3px}
.f-link{font-size:11px;color:var(--footer-text);white-space:nowrap}
.f-text{left:103px;top:4063px;width:330px;font-size:11px;line-height:23px;color:var(--footer-text)}
.copyright{left:103px;top:4261px;font-size:11px;color:var(--footer-text)}
.social-lead{left:777px;top:4261px;font-size:11px;color:var(--footer-text)}
.social-item{top:4261px;font-size:10px;font-weight:600;color:var(--orange)}
</style>
</head>
<body>

<!-- Header -->
<header class="abs site-header">
  <div class="abs brand"><span class="brand-dot"></span><span class="brand-name">KESTRAL FORD</span></div>
  <nav class="abs main-nav">
    <span class="nav-item">HOME</span>
    <span class="nav-item">ABOUT US</span>
    <span class="nav-item">SERVICES<span class="caret">&#8964;</span></span>
    <span class="nav-item">SITUATION MONITOR</span>
    <span class="nav-item">WORK WITH US</span>
    <span class="nav-item">CONTACT US</span>
  </nav>
  <div class="abs nav-phone">
    <svg width="18" height="18" viewBox="0 0 24 24"><path fill="#f39c1f" d="M6.6 10.8a15.1 15.1 0 0 0 6.6 6.6l2.2-2.2c.3-.3.7-.4 1-.2 1.1.4 2.3.6 3.6.6.6 0 1 .4 1 1V20c0 .6-.4 1-1 1A17 17 0 0 1 3 4c0-.6.4-1 1-1h3.5c.6 0 1 .4 1 1 0 1.3.2 2.5.6 3.6.1.3 0 .7-.2 1z"/></svg>
    <span>( 235 ) 555 - 0147</span>
  </div>
</header>

<!-- Hero -->
<div class="abs hero" role="img" aria-label="Paramedics loading a patient on a stretcher into an ambulance"></div>
<div class="abs hero-shade"></div>
<h1 class="abs hero-title center">KESTRAL FORD</h1>
<p class="abs hero-sub center">EMERGENCY MANAGEMENT CONSULTING COMPANY</p>
<a class="btn" style="left:437px;top:407px;width:152px;height:42px">Learn More</a>
<a class="btn" style="left:609px;top:407px;width:154px;height:42px">Contact Here</a>
<svg class="abs hero-arrow" style="left:62px" viewBox="0 0 20 28"><path d="M15 3 5 14l10 11" fill="none" stroke="#fff" stroke-width="2"/></svg>
<svg class="abs hero-arrow" style="left:1118px" viewBox="0 0 20 28"><path d="M5 3l10 11L5 25" fill="none" stroke="#fff" stroke-width="2"/></svg>
<div class="abs hero-down"><svg width="37" height="37" viewBox="0 0 37 37"><path d="M13 16l5.5 5.5L24 16" fill="none" stroke="#fff" stroke-width="1.6"/></svg></div>

<!-- Consulting -->
<section>
  <h2 class="abs heading center" style="top:760px;left:0;width:1200px;font-size:25px">Emergency Management Consulting</h2>
  <p class="abs para center" style="top:815px;left:215px;width:770px">Lorem Ipsum is simply dummy text of the printing and typesetting industry. Lorem Ipsum has been the industry's standard dummy text ever since the 1500s, when an unknown printer took a galley of type and scrambled it to make a type specimen book. It has survived not only five centuries, but also the leap into electronic typesetting, remaining essentially unchanged...</p>

  <svg class="abs" style="left:70px;top:1058px" width="20" height="26" viewBox="0 0 20 26"><path d="M14 3 5 13l9 10" fill="none" stroke="#b9b9b9" stroke-width="1.6"/></svg>
  <svg class="abs" style="left:1110px;top:1058px" width="20" height="26" viewBox="0 0 20 26"><path d="M6 3l9 10-9 10" fill="none" stroke="#b9b9b9" stroke-width="1.6"/></svg>

  <div class="abs service-icon" style="left:213px">
    <svg class="abs" style="left:32px;top:30px" width="50" height="54" viewBox="0 0 50 54"><path fill="#fff" d="M19 14h12v14h10v10H31v14H19V38H9V28h10z"/></svg>
  </div>
  <div class="abs service-icon" style="left:556px">
    <svg class="abs" style="left:29px;top:29px" width="56" height="56" viewBox="0 0 56 56"><path fill="#fff" d="M28 6C15 6 5 14 5 25c0 6 3 11 8 14l-2 10 10-7c2 .4 4 .6 7 .6 13 0 23-8 23-18S41 6 28 6z"/><path d="M33 32c0-6-4-9-10-9h-3l4-4M20 23l4 4" fill="none" stroke="#f39c1f" stroke-width="3"/></svg>
  </div>
  <div class="abs service-icon" style="left:899px">
    <svg class="abs" style="left:29px;top:29px" width="56" height="56" viewBox="0 0 56 56"><circle cx="28" cy="28" r="20" fill="none" stroke="#fff" stroke-width="4"/><path d="M28 16v13h9" fill="none" stroke="#fff" stroke-width="4"/></svg>
  </div>

  <h3 class="abs service-label center" style="left:105px">DISASTER PREPAREDNESS</h3>
  <h3 class="abs service-label center" style="left:448px">RESPONSE</h3>
  <h3 class="abs service-label center" style="left:791px">RECOVERY</h3>
  <p class="abs para center service-text" style="left:130px">Lorem Ipsum is simply dummy text of the printing and typesetting industry. Lorem Ipsum has been the industry...</p>
  <p class="abs para center service-text" style="left:473px">Lorem Ipsum is simply dummy text of the printing and typesetting industry. Lorem Ipsum has been the industry...</p>
  <p class="abs para center service-text" style="left:816px">Lorem Ipsum is simply dummy text of the printing and typesetting industry. Lorem Ipsum has been the industry...</p>
</section>

<!-- About -->
<section>
  <div class="abs about-photo" role="img" aria-label="Paramedics wheeling a stretcher out of an ambulance at sunset"></div>
  <h2 class="abs heading" style="left:665px;top:1313px;font-size:27px;font-weight:500">About</h2>
  <h3 class="abs heading" style="left:665px;top:1356px;font-size:20px">Kestral Ford Emergency Management</h3>
  <p class="abs para" style="left:666px;top:1399px;width:430px">Lorem Ipsum is simply dummy text of the printing and typesetting industry. Lorem Ipsum has been the industry's standard dummy text ever since the 1500s, when an unknown printer took a galley.</p>
  <p class="abs para" style="left:666px;top:1496px;width:430px">Lorem Ipsum is simply dummy text of the printing and typesetting industry. Lorem Ipsum has been the industry's standard dummy text ever since the 1500s, when an unknown printer took...</p>
  <a class="btn" style="left:666px;top:1599px;width:179px;height:42px">Read More Info</a>
</section>

<!-- Emergency management band -->
<section>
  <div class="abs band-photo" role="img" aria-label="Firefighters in protective gear with breathing tanks at a fire scene"></div>
  <div class="abs band-box">
    <h2 class="abs band-title">EMERGENCY MANAGEMENT</h2>
    <p class="abs band-text" style="top:87px">Lorem Ipsum is simply dummy text of the printing and typesetting industry. Lorem Ipsum has been the industry's standard dummy text ever since the 1500s, when an unknown printer took a galley.</p>
    <p class="abs band-text" style="top:176px">Lorem Ipsum is simply dummy text of the printing and typesetting industry. Lorem Ipsum has been the industry's standard dummy text ever since the 1500s...</p>
    <a class="abs band-btn">READ MORE INFO</a>
  </div>
</section>

<!-- Latest news -->
<section>
  <h2 class="abs heading center" style="top:2380px;left:0;width:1200px;font-size:27px;font-weight:500">Latest News</h2>
  <p class="abs para center" style="top:2432px;left:215px;width:770px">Lorem Ipsum is simply dummy text of the printing and typesetting industry. Lorem Ipsum has been the industry's standard dummy text ever since the 1500s, when an unknown printer took a galley of type and scrambled.</p>

  <div class="abs news-photo" style="left:98px;top:2535px;background:linear-gradient(135deg,#d9d24a,#c7b52c 40%,#6f6f6a 75%,#3d3d3d)" role="img" aria-label="Responders in yellow hazmat suits at a decontamination site"></div>
  <div class="abs news-photo" style="left:447px;top:2535px;background:linear-gradient(160deg,#2d6d93,#1d4f74 50%,#173d5c)" role="img" aria-label="Orange rescue helicopter flying over the sea"></div>
  <div class="abs news-photo" style="left:796px;top:2535px;background:linear-gradient(135deg,#2b2b2b,#555 45%,#a7262a 75%,#222)" role="img" aria-label="Two men in suits standing beside a red vehicle"></div>
  <div class="abs news-photo" style="left:98px;top:2837px;background:linear-gradient(135deg,#3e4244,#2b2e30 60%,#4a4d4f)" role="img" aria-label="Hand writing a risk management diagram on a chalkboard"></div>
  <div class="abs news-photo" style="left:447px;top:2837px;background:linear-gradient(135deg,#3d6b2f,#1f2c3d 50%,#2f3e4f)" role="img" aria-label="Two responders in navy uniforms talking outdoors"></div>
  <div class="abs news-photo" style="left:796px;top:2837px;background:linear-gradient(135deg,#c4261f,#9c1d18 50%,#5b5b5b)" role="img" aria-label="Red fire engine parked in a station"></div>

  <h3 class="abs news-title" style="left:98px;top:2762px">LOREM IPSUM IS SIMPLY DUMMY</h3>
  <h3 class="abs news-title" style="left:447px;top:2762px">LOREM IPSUM IS SIMPLY DUMMY</h3>
  <h3 class="abs news-title" style="left:796px;top:2762px">LOREM IPSUM IS SIMPLY DUMMY</h3>
  <p class="abs news-date" style="left:98px;top:2789px">Posted on 27 march 2016</p>
  <p class="abs news-date" style="left:447px;top:2789px">Posted on 27 march 2016</p>
  <p class="abs news-date" style="left:796px;top:2789px">Posted on 27 march 2016</p>

  <h3 class="abs news-title" style="left:98px;top:3065px">LOREM IPSUM IS SIMPLY DUMMY</h3>
  <h3 class="abs news-title" style="left:447px;top:3065px">LOREM IPSUM IS SIMPLY DUMMY</h3>
  <h3 class="abs news-title" style="left:796px;top:3065px">LOREM IPSUM IS SIMPLY DUMMY</h3>
  <p class="abs news-date" style="left:98px;top:3091px">Posted on 27 march 2016</p>
  <p class="abs news-date" style="left:447px;top:3091px">Posted on 27 march 2016</p>
  <p class="abs news-date" style="left:796px;top:3091px">Posted on 27 march 2016</p>
</section>

<!-- Testimonial -->
<section>
  <div class="abs quote-band" role="img" aria-label="Firefighters working in smoke beside fire trucks"></div>
  <div class="abs quote-shade"></div>
  <svg class="abs" style="left:575px;top:3297px" width="50" height="40" viewBox="0 0 50 40"><path fill="#f39c1f" d="M2 2h19v18c0 10-6 17-15 18l-1-6c5-1 8-5 8-10H2zM29 2h19v18c0 10-6 17-15 18l-1-6c5-1 8-5 8-10h-11z"/></svg>
  <p class="abs quote-text center">Lorem Ipsum es simplemente el texto de relleno de las imprentas y archivos de texto. Lorem Ipsum ha sido el texto de relleno estándar de las industrias</p>
  <p class="abs quote-author center">- Marlon Quist -</p>
  <span class="abs dot" style="left:578px;background:#ffffff"></span>
  <span class="abs dot" style="left:595px"></span>
  <span class="abs dot" style="left:612px"></span>
</section>

<!-- Situation monitor summary -->
<section>
  <h2 class="abs heading center monitor-title">Situation Monitor</h2>

  <article class="abs monitor-card" style="left:98px">
    <span class="abs monitor-tag">#wildfire</span>
    <span class="abs monitor-label">Mentions in the last 24 hours</span>
    <span class="abs monitor-count">1,284</span>
    <div class="abs monitor-bar"><span class="monitor-fill" style="width:78%"></span></div>
    <span class="abs monitor-note">Level: elevated</span>
  </article>
  <article class="abs monitor-card" style="left:447px">
    <span class="abs monitor-tag">flood warning</span>
    <span class="abs monitor-label">Mentions in the last 24 hours</span>
    <span class="abs monitor-count">642</span>
    <div class="abs monitor-bar"><span class="monitor-fill" style="width:46%"></span></div>
    <span class="abs monitor-note">Level: watch</span>
  </article>
  <article class="abs monitor-card" style="left:796px">
    <span class="abs monitor-tag">evacuation</span>
    <span class="abs monitor-label">Mentions in the last 24 hours</span>
    <span class="abs monitor-count">215</span>
    <div class="abs monitor-bar"><span class="monitor-fill" style="width:22%"></span></div>
    <span class="abs monitor-note">Level: normal</span>
  </article>
</section>

<!-- Footer -->
<footer>
  <div class="abs site-footer"></div>
  <h4 class="abs f-title" style="left:103px">WHO WE ARE?</h4>
  <p class="abs f-text">Lorem Ipsum is simply dummy text of the printing and typesetting industry. Lorem Ipsum has been the industry's standard dummy text ever since the 1500s, when an unknown printer took a galley of type and scrambled...</p>
  <a class="abs f-link" style="left:104px;top:4170px;color:var(--orange)">Read more info &nbsp;<svg width="10" height="10" viewBox="0 0 10 10"><circle cx="5" cy="5" r="5" fill="#f39c1f"/><path d="M4 3l2 2-2 2" fill="none" stroke="#2c2c2c" stroke-width="1.3"/></svg></a>

  <h4 class="abs f-title" style="left:532px">WELCOME</h4>
  <a class="abs f-link" style="left:532px;top:4064px">Home</a>
  <a class="abs f-link" style="left:532px;top:4088px">About Us</a>
  <a class="abs f-link" style="left:532px;top:4112px">Services</a>
  <a class="abs f-link" style="left:532px;top:4136px">Situation Monitor</a>
  <a class="abs f-link" style="left:532px;top:4160px">Work With Us</a>
  <a class="abs f-link" style="left:532px;top:4184px">Contact Us</a>

  <h4 class="abs f-title" style="left:711px">INFORMATION</h4>
  <a class="abs f-link" style="left:711px;top:4064px">Terms &amp; Conditions</a>
  <a class="abs f-link" style="left:711px;top:4088px">Privacy policy</a>
  <a class="abs f-link" style="left:711px;top:4112px">Disclaimer</a>
  <a class="abs f-link" style="left:711px;top:4136px">Sitemap</a>

  <h4 class="abs f-title" style="left:900px">CONTACT INFO</h4>
  <p class="abs f-link" style="left:900px;top:4066px">120 Street name, City name,</p>
  <p class="abs f-link" style="left:900px;top:4092px">Country name : 3652235</p>
  <p class="abs f-link" style="left:900px;top:4120px;display:flex;gap:10px;align-items:center"><svg width="11" height="11" viewBox="0 0 24 24"><path fill="#f39c1f" d="M6.6 10.8a15.1 15.1 0 0 0 6.6 6.6l2.2-2.2c.3-.3.7-.4 1-.2 1.1.4 2.3.6 3.6.6.6 0 1 .4 1 1V20c0 .6-.4 1-1 1A17 17 0 0 1 3 4c0-.6.4-1 1-1h3.5c.6 0 1 .4 1 1 0 1.3.2 2.5.6 3.6.1.3 0 .7-.2 1z"/></svg>( 235 ) 555 - 0147</p>
  <p class="abs f-link" style="left:900px;top:4148px;display:flex;gap:10px;align-items:center"><svg width="12" height="9" viewBox="0 0 12 9"><rect width="12" height="9" fill="#f39c1f"/><path d="M0 0l6 5 6-5" fill="none" stroke="#2c2c2c" stroke-width="1"/></svg>info@kestralford.example</p>

  <div class="abs footer-bar"></div>
  <p class="abs copyright">© 2017, Kestral Ford. All rights reserved</p>
  <p class="abs social-lead">Connect with our social network :</p>
  <span class="abs social-item" style="left:952px">Page</span>
  <span class="abs social-item" style="left:986px">Feed</span>
  <span class="abs social-item" style="left:1020px">Plus</span>
  <span class="abs social-item" style="left:1054px">Pins</span>
  <span class="abs social-item" style="left:1088px">Work</span>
</footer>

</body>
</html>
```